Tall Fern Roofing Business Card

Need a business card with the logo that was designed here

Contact Information for Business Card

Name, Title, Phone, Email, Website, Company name

```html
<!DOCTYPE html>
<html lang="en">
<head>
<meta charset="utf-8">
<title>Tall Fern Roofing – Business Card</title>
<link href="https://fonts.googleapis.com/css2?family=Montserrat:wght@400;500;700&display=swap" rel="stylesheet">
<style>
  :root {
    --backdrop: #d5d8d9;
    --card: #fbfbfb;
    --brand-blue: #1d3a9c;
    --ink: #3a3a3a;
    --muted: #6b6b6b;
  }
  * { box-sizing: border-box; margin: 0; padding: 0; }
  html, body { width: 1200px; height: 829px; overflow: hidden; }
  body {
    background: var(--backdrop);
    font-family: "Montserrat", sans-serif;
    position: relative;
  }
  .card {
    position: absolute;
    width: 520px;
    height: 297px;
    background: var(--card);
    border-bottom: 5px solid var(--brand-blue);
    box-shadow: 0 10px 28px rgba(0,0,0,0.12);
    overflow: hidden;
  }
  .card--contact { left: 50px; top: 266px; }
  .card--brand { left: 630px; top: 266px; }

  .wordmark {
    display: flex;
    align-items: center;
    gap: 10px;
    color: var(--brand-blue);
    font-weight: 700;
    text-transform: uppercase;
    letter-spacing: 0.06em;
  }
  .wordmark__square {
    width: 14px; height: 14px;
    background: var(--brand-blue);
    flex: none;
  }
  .card--brand .wordmark {
    position: absolute;
    left: 0; right: 0; top: 0; bottom: 0;
    justify-content: center;
    font-size: 30px;
  }
  .card--brand .wordmark__square { width: 22px; height: 22px; }

  .card--contact .wordmark {
    position: absolute;
    left: 40px; top: 34px;
    font-size: 17px;
  }
  .divider {
    position: absolute;
    left: 40px; right: 70px; top: 88px;
    height: 1px;
    background: var(--brand-blue);
  }
  .address {
    position: absolute;
    left: 40px; top: 106px;
    font-size: 12.5px;
    line-height: 1.5;
    color: var(--muted);
  }
  .contacts {
    position: absolute;
    left: 40px; top: 160px;
    list-style: none;
    font-size: 12.5px;
    line-height: 1.6;
    color: var(--muted);
  }
  .contacts li { display: flex; align-items: center; gap: 7px; }
  .contacts svg { width: 10px; height: 10px; fill: var(--brand-blue); flex: none; }

  .person {
    position: absolute;
    right: 38px; top: 120px;
    text-align: right;
  }
  .person__name {
    font-size: 17px;
    font-weight: 700;
    letter-spacing: 0.05em;
    color: var(--brand-blue);
  }
  .person__title {
    font-size: 12.5px;
    color: var(--muted);
    margin-top: 2px;
  }
  .accent-bar {
    position: absolute;
    right: 0; top: 120px;
    width: 12px; height: 40px;
    background: var(--brand-blue);
  }
  .base-band {
    position: absolute;
    left: 0; bottom: 0;
    width: 100%; height: 40px;
  }
</style>
</head>
<body>

  <section class="card card--contact">
    <div class="wordmark"><span class="wordmark__square"></span>Tall Fern Roofing</div>
    <div class="divider"></div>

    <p class="address">418 Harlow Avenue<br>Wexford County 5230</p>

    <ul class="contacts">
      <li>
        <svg viewBox="0 0 10 10"><path d="M2 0.5 L3.6 2.6 L2.7 3.6 Q3.8 5.9 6.3 7.3 L7.4 6.4 L9.5 8 L8.3 9.5 Q3.8 9 0.5 1.6 Z"/></svg>
        0481 552 907
      </li>
      <li>
        <svg viewBox="0 0 10 10"><path d="M0.5 2 H9.5 V8 H0.5 Z M1 2.4 L5 5.4 L9 2.4" stroke="#fff" stroke-width="0.7"/></svg>
        info@tallfernroofing.com
      </li>
      <li>
        <svg viewBox="0 0 10 10"><circle cx="5" cy="5" r="4.5"/><path d="M0.5 5 H9.5 M5 0.5 Q2.5 5 5 9.5 M5 0.5 Q7.5 5 5 9.5" stroke="#fff" stroke-width="0.6" fill="none"/></svg>
        www.tallfernroofing.com
      </li>
    </ul>

    <div class="person">
      <p class="person__name">DECLAN MARSH</p>
      <p class="person__title">Managing Director</p>
    </div>
    <div class="accent-bar"></div>

    <svg class="base-band" viewBox="0 0 520 40" preserveAspectRatio="none">
      <path d="M0 22 H300 L330 8" fill="none" stroke="var(--brand-blue)" stroke-width="4"/>
      <rect x="0" y="34" width="520" height="6" fill="var(--brand-blue)"/>
    </svg>
  </section>

  <section class="card card--brand">
    <div class="wordmark"><span class="wordmark__square"></span>Tall Fern Roofing</div>
  </section>

</body>
</html>
```